Remodel Flyer for realtors

"R" Anchored Builders

4"x 9" rack card front and back

www.BrevinHomeworks.com

555-318-4762

Let us fix what your home inspector finds!

Send us your inspection summary.

We are a licensed and Insured contractor.
CRC4870213

Serving
Marion County and The Hollows

This flyer will sit in realtor offices for realtors to give to there buyers and sellers.

Target Market(s)

Realtors

Industry/Entity Type

Construction

Colors

Designer to choose colors to be used in the design.

```html
<!DOCTYPE html>
<html lang="en">
<head>
<meta charset="utf-8">
<title>R Anchored Builders – Rack Card</title>
<link href="https://fonts.googleapis.com/css2?family=Roboto:wght@700&display=swap" rel="stylesheet">
<style>
  :root {
    --stage: #e9e9e9;
    --orange: #ee8f22;
    --orange-deep: #b85a12;
    --rust: #6b2e14;
    --charcoal: #333333;
    --ink: #434343;
    --paper: #f1f1f1;
    --cream: #f3e7d6;
    --mist: #e0e0e0;
  }
  * { box-sizing: border-box; margin: 0; padding: 0; }
  html, body {
    width: 1200px; height: 1000px; overflow: hidden;
    background: var(--stage);
    font-family: "Roboto", Arial, sans-serif;
  }
  .rack-card {
    position: absolute; top: 143px;
    width: 313px; height: 710px; overflow: hidden;
  }
  .rack-card--front { left: 276px; }
  .rack-card--back { left: 624px; background: var(--cream); }
  .card-shapes { position: absolute; inset: 0; display: block; }

  .brand {
    position: absolute; left: 0; right: 0; top: 268px;
    text-align: center; color: var(--ink); font-weight: 700;
  }
  .brand__mark {
    width: 96px; height: 96px; margin: 0 auto 22px;
    background: var(--orange);
  }
  .brand__name { font-size: 30px; letter-spacing: 1px; line-height: 1; }
  .brand__trade { font-size: 17px; letter-spacing: 9px; margin-top: 12px; padding-left: 9px; }

  .feature {
    position: absolute; left: 0; right: 0;
    text-align: center; color: var(--ink);
    font-size: 14.5px; font-weight: 700; line-height: 19px;
  }
  .feature__icon { display: block; margin: 0 auto 10px; }
  .feature--fix { top: 50px; }
  .feature--summary { top: 180px; }
  .feature--area { top: 314px; }
  .feature--contact { top: 444px; }
  .feature--license { top: 579px; }
  .license-seal {
    display: block; width: 48px; height: 48px; margin: 0 auto 10px;
    border-radius: 50%; background: var(--orange);
  }
</style>
</head>
<body>

<section class="rack-card rack-card--front" aria-label="Rack card front">
  <svg class="card-shapes" viewBox="0 0 313 710" width="313" height="710">
    <defs>
      <linearGradient id="steelGlow" x1="0" y1="0" x2="1" y2="1">
        <stop offset="0" stop-color="var(--rust)"/>
        <stop offset="0.45" stop-color="var(--orange-deep)"/>
        <stop offset="1" stop-color="var(--orange)"/>
      </linearGradient>
    </defs>
    <rect class="photo-fill" width="313" height="710" fill="url(#steelGlow)" role="img" aria-label="Photo of steel building frame beams against an orange sunset sky"/>
    <polygon class="center-panel" points="0,247 313,72 313,470 0,640" fill="var(--paper)" stroke="#ffffff" stroke-width="6"/>
    <polygon class="accent-triangle" points="165,158 313,76 313,242" fill="var(--charcoal)"/>
    <polygon class="accent-triangle" points="0,468 150,552 0,636" fill="var(--charcoal)"/>
  </svg>
  <div class="brand">
    <div class="brand__mark"></div>
    <div class="brand__name">R ANCHORED</div>
    <div class="brand__trade">BUILDERS</div>
  </div>
</section>

<section class="rack-card rack-card--back" aria-label="Rack card back">
  <svg class="card-shapes" viewBox="0 0 313 710" width="313" height="710" aria-hidden="true">
    <polygon points="0,72 313,243 313,637 0,467" fill="var(--paper)"/>
    <polygon points="0,72 150,157 0,242" fill="var(--mist)"/>
    <polygon points="313,467 165,552 313,637" fill="var(--mist)"/>
  </svg>

  <div class="feature feature--fix">
    <svg class="feature__icon" width="46" height="46" viewBox="0 0 46 46" aria-hidden="true">
      <g fill="var(--orange)">
        <circle cx="23" cy="23" r="17"/>
        <g>
          <rect x="19" y="1" width="8" height="8"/><rect x="19" y="37" width="8" height="8"/>
          <rect x="1" y="19" width="8" height="8"/><rect x="37" y="19" width="8" height="8"/>
          <g transform="rotate(45 23 23)">
            <rect x="19" y="1" width="8" height="8"/><rect x="19" y="37" width="8" height="8"/>
            <rect x="1" y="19" width="8" height="8"/><rect x="37" y="19" width="8" height="8"/>
          </g>
        </g>
      </g>
      <circle cx="23" cy="23" r="10" fill="#ffffff"/>
    </svg>
    Let Us Fix<br>What Your Home Inspector Finds!
  </div>

  <div class="feature feature--summary">
    <svg class="feature__icon" width="34" height="46" viewBox="0 0 34 46" aria-hidden="true">
      <rect x="2" y="2" width="30" height="42" rx="3" fill="none" stroke="var(--orange)" stroke-width="3"/>
      <g stroke="var(--orange)" stroke-width="3">
        <line x1="9" y1="12" x2="25" y2="12"/><line x1="9" y1="19" x2="25" y2="19"/>
        <line x1="9" y1="26" x2="25" y2="26"/><line x1="9" y1="33" x2="25" y2="33"/>
      </g>
    </svg>
    Send Us Your<br>Inspection Summary.
  </div>

  <div class="feature feature--area">
    <svg class="feature__icon" width="46" height="46" viewBox="0 0 46 46" aria-hidden="true">
      <circle cx="23" cy="23" r="22" fill="var(--orange)"/>
      <circle cx="23" cy="18" r="6" fill="#ffffff"/>
      <path d="M13 33 a10 9 0 0 1 20 0 z" fill="#ffffff"/>
    </svg>
    Serving Marion County<br>and The Hollows
  </div>

  <div class="feature feature--contact">
    <svg class="feature__icon" width="42" height="42" viewBox="0 0 42 42" aria-hidden="true">
      <g fill="none" stroke="var(--orange)" stroke-width="2.5">
        <circle cx="21" cy="21" r="18"/>
        <ellipse cx="21" cy="21" rx="8" ry="18"/>
        <line x1="21" y1="3" x2="21" y2="39"/>
        <line x1="3" y1="21" x2="39" y2="21"/>
        <path d="M6 12 h30 M6 30 h30"/>
      </g>
    </svg>
    555-318-4762<br>www.BrevinHomeworks.com
  </div>

  <div class="feature feature--license">
    <span class="license-seal"></span>
    We are a licensed and Insured contractor.<br>CRC4870213
  </div>
</section>

</body>
</html>
```